Alloy wheel repair business needs a website

Install logo previously purchased from makerhive, toolbar with dropdowns. services, gallery, clients , contact ect
Maybe mission statment

Target Market(s)

vehicle owners, auto dealers,insurance companies,

Industry/Entity Type

Alloy Wheel Repair

Coding

Coded - Design and coding required

Number of Pages Required

4 page

Font styles to use
Sans Serif

Colors
0054AA
0677BA
7BADD7
CADEEF
E8F1F8

```html
<!DOCTYPE html>
<html lang="en">
<head>
<meta charset="utf-8">
<title>Rimline Wheelworks</title>
<link href="https://fonts.googleapis.com/css2?family=Audiowide&family=Lato:wght@400;700;900&display=swap" rel="stylesheet">
<style>
:root{
  --blue:#3f86cc;
  --blue-deep:#0054aa;
  --blue-mid:#0677ba;
  --blue-soft:#7badd7;
  --blue-pale:#cadeef;
  --blue-mist:#e8f1f8;
  --ink:#1b1b1b;
  --text:#3a3a3a;
  --grey-band:#eeeeef;
  --line:#c9c9c9;
  --dark:#1d1e20;
}
*{margin:0;padding:0;box-sizing:border-box}
html,body{width:1200px;height:3945px;overflow:hidden}
body{position:relative;background:#fff;font-family:"Lato",sans-serif;color:var(--text)}
.abs{position:absolute}
.display{font-family:"Audiowide",sans-serif;font-weight:400}
.btn{position:absolute;background:var(--blue);color:#fff;border-radius:40px;font-family:"Audiowide",sans-serif;font-size:14px;display:flex;align-items:center;justify-content:center}

/* header */
.site-header{position:absolute;left:0;top:0;width:1200px;height:116px;background:#fff}
.brand{position:absolute;display:flex;align-items:center;gap:10px;font-family:"Lato",sans-serif;font-weight:900;color:var(--blue);font-size:24px;letter-spacing:1px;line-height:1}
.brand-dot{width:22px;height:22px;border-radius:50%;background:var(--blue)}
.nav a{position:absolute;top:0;height:116px;display:flex;align-items:center;justify-content:center;font-size:14px;color:#444;text-decoration:none}
.nav a.active{background:var(--blue);color:#fff}
.phone-btn{left:897px;top:38px;width:191px;height:40px;font-family:"Lato",sans-serif;font-weight:700;font-size:15px;gap:8px}

/* hero */
.hero-blue{left:0;top:116px;width:1200px;height:569px;background:var(--blue);border-bottom-left-radius:330px}
.hero-dark{left:0;top:116px;width:1200px;height:556px;background:#050505;border-bottom-left-radius:330px;margin-left:0;overflow:hidden}
.hero-blue-wrap{left:0;top:116px;width:1200px;height:569px;background:#fff}
.hero-photo{left:628px;top:0;width:572px;height:556px;background:radial-gradient(circle at 60% 45%,#9a9a9a 0%,#5a5a5a 30%,#2a2a2a 60%,#0a0a0a 100%)}
.hero-title{left:112px;top:262px;font-size:52px;line-height:1.02;color:var(--blue)}
.hero-rule{left:112px;top:393px;width:391px;height:3px;background:var(--blue)}
.hero-text{left:112px;top:416px;width:420px;font-size:17px;line-height:29px;color:#fff}
.scroll-btn{left:572px;top:659px;width:56px;height:57px;background:var(--blue);border-radius:6px;display:flex;align-items:center;justify-content:center}

/* partners */
.partners{left:0;top:685px;width:1200px;height:281px;background:var(--grey-band);border-bottom:4px solid var(--blue)}
.badge{position:absolute;background:#cfcfd4}

/* services intro */
.intro{left:0;top:970px;width:1200px;height:755px;background:linear-gradient(#f6f6f6,#f1f1f1)}
.section-title{position:absolute;width:1200px;left:0;text-align:center;color:var(--blue);font-size:34px}
.intro-text{left:190px;top:1110px;width:820px;text-align:center;font-size:16px;line-height:29px;color:#333}
.video{left:219px;top:1205px;width:762px;height:425px;background:linear-gradient(120deg,#1e2329 0%,#3b4048 45%,#262a31 70%,#121418 100%);box-shadow:0 10px 18px rgba(0,0,0,.35)}
.play{left:569px;top:1381px;width:62px;height:62px;border-radius:50%;background:#fff;display:flex;align-items:center;justify-content:center}

/* mission */
.mission-title{left:112px;top:1848px;font-size:34px;color:var(--blue)}
.mission-text{left:112px;top:1906px;width:481px;font-size:16px;line-height:29px;text-align:justify;color:#333}
.mission-photo{left:630px;top:1835px;width:465px;height:331px;border-top-left-radius:140px;border-top-right-radius:10px;background:linear-gradient(135deg,#3b3222 0%,#6b5a3e 35%,#3e4a55 70%,#1e2630 100%)}
.wheel-photo{border-radius:50%;background:radial-gradient(circle,#3c3c3c 0 12%,#d9d9d9 13% 60%,#8a8a8a 61% 72%,#2a2a2a 73% 100%)}

/* services dark */
.services{left:0;top:2315px;width:1200px;height:572px;background:repeating-linear-gradient(45deg,#202124 0 3px,#18191b 3px 6px)}
.card{position:absolute;top:2487px;width:217px;height:231px;border:1.5px solid var(--blue-mid);border-radius:22px}
.card-rule{position:absolute;left:0;right:0;top:160px;height:1.5px;background:var(--blue-mid)}
.card-icon{position:absolute;left:58px;top:30px}
.card-label{position:absolute;left:0;right:0;top:160px;bottom:0;display:flex;align-items:center;justify-content:center;text-align:center;font-family:"Audiowide",sans-serif;color:#fff;font-size:16px;line-height:25px}

/* contact */
.contact-photo{left:0;top:2887px;width:582px;height:636px;border-bottom-right-radius:230px;background:linear-gradient(135deg,#2b2b2b 0%,#7a7a7a 30%,#3a2a22 55%,#8d8d8d 75%,#202020 100%)}
.contact-title{left:639px;top:2996px;font-size:34px;color:var(--ink)}
.contact-text{left:643px;top:3060px;width:420px;font-size:16px;line-height:29px;color:#333}
.field{position:absolute;border:1.5px solid #c6c6c6;border-radius:4px;font-size:16px;color:#9a9a9a;padding:14px 18px}

/* footer */
.foot-head{position:absolute;top:3630px;font-weight:700;font-size:17px;color:var(--ink)}
.foot-list{position:absolute;top:3666px;list-style:none;font-size:17px;line-height:29px;color:#444}
.foot-text{left:112px;top:3710px;width:260px;font-size:14px;line-height:26px;color:#444}
.foot-bar{left:0;top:3878px;width:1200px;height:2px;background:var(--blue-pale)}
.copyright{left:0;top:3896px;width:1200px;text-align:center;font-size:15px;color:#444}
</style>
</head>
<body>

<header class="site-header">
  <div class="brand" style="left:117px;top:44px"><span class="brand-dot"></span>RIMLINE WHEELWORKS</div>
  <nav class="nav">
    <a class="active" href="#" style="left:448px;width:72px">Home</a>
    <a href="#" style="left:530px;width:70px">Services</a>
    <a href="#" style="left:618px;width:60px">Gallery</a>
    <a href="#" style="left:697px;width:56px">Clients</a>
    <a href="#" style="left:776px;width:60px">Contact</a>
  </nav>
  <div class="btn phone-btn">
    <svg width="14" height="14" viewBox="0 0 24 24"><path fill="#fff" d="M6.6 10.8a15.1 15.1 0 0 0 6.6 6.6l2.2-2.2a1 1 0 0 1 1-.25 11.4 11.4 0 0 0 3.6.57 1 1 0 0 1 1 1V20a1 1 0 0 1-1 1A17 17 0 0 1 3 4a1 1 0 0 1 1-1h3.5a1 1 0 0 1 1 1c0 1.25.2 2.45.57 3.57a1 1 0 0 1-.25 1z"/></svg>
    (+1) 555 010 2030
  </div>
</header>

<section>
  <div class="abs hero-blue-wrap"></div>
  <div class="abs hero-blue"></div>
  <div class="abs hero-dark">
    <div class="abs hero-photo" role="img" aria-label="Close-up of a polished alloy wheel with brake disc"></div>
  </div>
  <h1 class="abs display hero-title">Welcome to<br>Rimline Wheelworks</h1>
  <div class="abs hero-rule"></div>
  <p class="abs hero-text">Lorem ipsum dolor sit amet, consectetur adipiscing elit, sed do eiusmod tempor incididunt ut.</p>
  <div class="btn" style="left:112px;top:498px;width:156px;height:42px">Get Started</div>
  <div class="abs scroll-btn">
    <svg width="18" height="22" viewBox="0 0 18 22"><path d="M9 2v17M2 12l7 7 7-7" stroke="#fff" stroke-width="2" fill="none"/></svg>
  </div>
</section>

<section class="abs partners" aria-label="Partners">
  <div class="badge" style="left:160px;top:100px;width:48px;height:48px;border-radius:8px"></div>
  <div class="badge" style="left:417px;top:100px;width:48px;height:48px;border-radius:50%"></div>
  <div class="badge" style="left:660px;top:100px;width:48px;height:48px;border-radius:50%"></div>
  <div class="badge" style="left:948px;top:100px;width:48px;height:48px;border-radius:8px"></div>
</section>

<section>
  <div class="abs intro"></div>
  <h2 class="section-title display" style="top:1048px">Rimline Wheelworks Services</h2>
  <p class="abs intro-text">Lorem ipsum dolor sit amet, consectetur adipiscing elit, sed do eiusmod tempor incididunt ut labore et dolore magna aliqua. Quis ipsum suspendisse ultrices gravida.</p>
  <div class="abs video" role="img" aria-label="Video still of a technician fitting a tyre on an alloy wheel"></div>
  <div class="abs play"><svg width="22" height="24" viewBox="0 0 22 24"><path d="M4 2l16 10L4 22z" fill="#111"/></svg></div>
</section>

<section>
  <h2 class="abs display mission-title">Our Mission</h2>
  <p class="abs mission-text">Lorem ipsum dolor sit amet, consectetur adipiscing elit, sed do eiusmod tempor incididunt ut labore et dolore magna aliqua. Quis ipsum suspendisse ultrices gravida. Risus commodo viverra maecenas accumsan lacus vel facilisis. Lorem ipsum dolor sit amet, consectetur adipiscing elit, sed do eiusmod tempor incididunt ut labore et dolore magna aliqua.</p>
  <div class="btn" style="left:113px;top:2108px;width:157px;height:42px">Read More</div>
  <div class="abs mission-photo" role="img" aria-label="Wheel technician in a workshop"></div>
  <div class="abs wheel-photo" role="img" aria-label="Silver alloy wheel" style="left:981px;top:2061px;width:162px;height:162px"></div>
</section>

<section>
  <div class="abs services"></div>
  <h2 class="section-title display" style="top:2378px">Our Services</h2>

  <div class="card" style="left:133px">
    <svg class="card-icon" width="100" height="100" viewBox="0 0 100 100"><circle cx="50" cy="50" r="48" fill="#fff"/><circle cx="50" cy="50" r="36" fill="none" stroke="#222" stroke-width="6"/><circle cx="50" cy="50" r="8" fill="#222"/><g fill="#222"><circle cx="50" cy="28" r="8"/><circle cx="71" cy="43" r="8"/><circle cx="63" cy="68" r="8"/><circle cx="37" cy="68" r="8"/><circle cx="29" cy="43" r="8"/></g></svg>
    <div class="card-rule"></div><div class="card-label">Wheel Refinishing</div>
  </div>
  <div class="card" style="left:374px">
    <svg class="card-icon" width="100" height="100" viewBox="0 0 100 100" fill="none" stroke="#fff" stroke-width="3"><rect x="10" y="78" width="82" height="12"/><path d="M18 78V20h14v58M18 40h40"/><circle cx="68" cy="40" r="20"/><circle cx="68" cy="40" r="6"/><path d="M30 62h40v16"/></svg>
    <div class="card-rule"></div><div class="card-label">Wheel Straightening</div>
  </div>
  <div class="card" style="left:615px">
    <svg class="card-icon" width="100" height="100" viewBox="0 0 100 100" fill="none" stroke="#fff" stroke-width="3"><circle cx="50" cy="50" r="46"/><circle cx="50" cy="50" r="36"/><circle cx="50" cy="50" r="7"/><path d="M50 43V15M56 48l27-9M54 56l16 23M46 56L30 79M44 48l-27-9"/></svg>
    <div class="card-rule"></div><div class="card-label">Wheel<br>Remanufacturing</div>
  </div>
  <div class="card" style="left:855px">
    <svg class="card-icon" width="100" height="100" viewBox="0 0 100 100" fill="none" stroke="#fff" stroke-width="3"><path d="M50 14a36 36 0 1 0 4 72c6 0 6-8 2-12-4-4 0-10 6-10h10a16 16 0 0 0 14-18C84 28 68 14 50 14z"/><circle cx="34" cy="40" r="5"/><circle cx="32" cy="60" r="5"/><path d="M58 58l30-30"/></svg>
    <div class="card-rule"></div><div class="card-label">Wheel Custom<br>Coloring</div>
  </div>

  <div class="btn" style="left:523px;top:2781px;width:155px;height:41px">View More</div>
  <div class="abs wheel-photo" role="img" aria-label="Silver alloy wheel" style="left:1043px;top:2796px;width:162px;height:162px"></div>
</section>

<section>
  <div class="abs contact-photo" role="img" aria-label="Stacked alloy wheels on display racks"></div>
  <h2 class="abs display contact-title">Contact Us</h2>
  <p class="abs contact-text">Lorem ipsum dolor sit amet, consectetur adipiscing elit, sed do eiusmod tempor incididunt.</p>
  <div class="field" style="left:636px;top:3149px;width:221px;height:47px">First Name</div>
  <div class="field" style="left:872px;top:3149px;width:223px;height:47px">Last Name</div>
  <div class="field" style="left:636px;top:3210px;width:221px;height:48px">Email</div>
  <div class="field" style="left:872px;top:3210px;width:223px;height:48px">Phone</div>
  <div class="field" style="left:636px;top:3273px;width:459px;height:95px">Message</div>
  <div class="btn" style="left:754px;top:3394px;width:209px;height:42px;border-radius:4px;font-size:16px">Submit</div>
</section>

<footer>
  <svg class="abs" style="left:990px;top:3523px" width="210" height="250" viewBox="0 0 210 250"><path d="M0 0C110 0 200 90 210 250V0z" fill="var(--blue)"/></svg>
  <div class="brand" style="left:115px;top:3660px"><span class="brand-dot"></span>RIMLINE WHEELWORKS</div>
  <p class="abs foot-text">Lorem ipsum dolor sit amet, consectetur adipiscing elit, sed do eiusmod tempor incididunt ut labore et.</p>
  <div class="foot-head" style="left:463px">Company</div>
  <ul class="foot-list" style="left:463px"><li>Home</li><li>Services</li><li>Gallery</li><li>Clients</li><li>Contact</li></ul>
  <div class="foot-head" style="left:642px">Services</div>
  <ul class="foot-list" style="left:642px"><li>Wheel Refinishing</li><li>Wheel Straightening</li><li>Wheel Remanufacturing</li><li>Wheel Custom Coloring</li></ul>
  <div class="foot-head" style="left:937px">Legal</div>
  <ul class="foot-list" style="left:937px"><li>Privacy Policy</li><li>Support</li><li>Terms &amp; Conditions</li></ul>
  <div class="abs foot-bar"></div>
  <p class="abs copyright">© Copyrights 2023 Rimline Wheelworks | All Rights Reserved</p>
</footer>

</body>
</html>
```